BuildLinkHub.com Full Stationery Design

Business Card will have all info on it. Letterhead will not have name, title or mobile number. Keep general feeling very clean, using colors from the logo as accents.
Name:Dale Marchetti
Title:President
Phone: 1-800-555-0142
Cell: 306-555-0187
email: dale@buildlinkhub.example
website: www.buildlinkhub.example
Address:
PO Box 947
Larchmere, KT
S0J2T0

Target Market(s)

Construction Business owners

Industry/Entity Type

Business

Contact Information for Business Card

Name:Dale Marchetti
Title:President
Phone: 1-800-555-0142
Cell: 306-555-0187
Address:
PO Box 947
Larchmere, KT
S0J2T0

Font styles to use
Sans Serif

Requirements
Must have
• Clean look
Should not have
• Images or cartoon type characters or tools

```html
<!DOCTYPE html>
<html lang="en">
<head>
<meta charset="utf-8">
<title>BuildLinkHub.com Business Card</title>
<link href="https://fonts.googleapis.com/css2?family=Open+Sans:wght@400;600;700&display=swap" rel="stylesheet">
<style>
  :root {
    --backdrop: #5f4e3d;
    --card-white: #ffffff;
    --slate: #4a5a6c;
    --ink: #4a5568;
    --text-grey: #555e69;
    --accent-red: #e8262d;
    --accent-orange: #f58220;
    --name-red: #e8412c;
  }
  * { margin: 0; padding: 0; box-sizing: border-box; }
  html, body { width: 1200px; height: 987px; overflow: hidden; }
  body {
    background: var(--backdrop);
    font-family: "Open Sans", Arial, sans-serif;
    position: relative;
  }
  .card {
    position: absolute;
    left: 293px;
    width: 615px;
    height: 352px;
  }
  .card--front { top: 130px; background: var(--card-white); }
  .card--back { top: 506px; background: var(--slate); }

  .brand-mark {
    position: absolute;
    top: 44px;
    right: 35px;
    display: flex;
    align-items: center;
    gap: 12px;
  }
  .brand-square {
    width: 34px;
    height: 34px;
    background: var(--accent-orange);
  }
  .brand-name {
    font-weight: 700;
    font-size: 30px;
    color: var(--slate);
    letter-spacing: -0.2px;
  }

  .person { position: absolute; left: 35px; top: 197px; }
  .person-name {
    font-weight: 600;
    font-size: 23px;
    color: var(--ink);
    line-height: 1.2;
  }
  .person-title {
    font-size: 17px;
    color: var(--name-red);
    line-height: 1.3;
  }

  .contact-list {
    position: absolute;
    right: 36px;
    top: 200px;
    list-style: none;
    text-align: right;
  }
  .contact-item {
    display: flex;
    justify-content: flex-end;
    align-items: center;
    gap: 8px;
    font-size: 15.5px;
    color: var(--text-grey);
    height: 24px;
  }
  .contact-item svg { width: 16px; height: 16px; fill: var(--ink); }
  .contact-item--address { margin-top: 3px; }

  .web-band {
    position: absolute;
    left: 35px;
    top: 291px;
    width: 215px;
    height: 30px;
    background: linear-gradient(90deg, var(--accent-red), var(--accent-orange));
    color: #fff;
    font-size: 15px;
    line-height: 30px;
    padding-left: 10px;
    white-space: nowrap;
  }
  .rule {
    position: absolute;
    left: 250px;
    top: 306px;
    width: 329px;
    height: 1px;
    background: var(--slate);
  }

  .back-brand {
    position: absolute;
    right: 42px;
    top: 235px;
    text-align: left;
    color: #fff;
  }
  .back-brand-name {
    font-weight: 700;
    font-size: 36px;
    line-height: 1.1;
  }
  .back-url {
    font-size: 17px;
    margin-top: 6px;
  }
</style>
</head>
<body>
  <section class="card card--front">
    <div class="brand-mark">
      <span class="brand-square"></span>
      <span class="brand-name">BuildLinkHub.com</span>
    </div>

    <div class="person">
      <p class="person-name">Dale Marchetti</p>
      <p class="person-title">President</p>
    </div>

    <ul class="contact-list">
      <li class="contact-item">1-800-555-0142
        <svg viewBox="0 0 16 16"><path d="M3.5 1.5l2.5 0 1 3.5-1.6 1.2c.8 1.8 2.2 3.2 4 4l1.2-1.6 3.4 1v2.6c0 .6-.5 1-1.1 1C7.3 13.2 2.8 8.7 2.5 2.6c0-.6.4-1.1 1-1.1z"/></svg>
      </li>
      <li class="contact-item">306-555-0187
        <svg viewBox="0 0 16 16"><path d="M4.5 1h7c.6 0 1 .4 1 1v12c0 .6-.4 1-1 1h-7c-.6 0-1-.4-1-1V2c0-.6.4-1 1-1zm.8 1.6v9.6h5.4V2.6z"/></svg>
      </li>
      <li class="contact-item">dale@buildlinkhub.example
        <svg viewBox="0 0 16 16"><path d="M1 4h14v9H1zm1.2 1L8 9l5.8-4z"/></svg>
      </li>
      <li class="contact-item contact-item--address">PO Box 947, Larchmere, KT, S0J2T0</li>
    </ul>

    <div class="web-band">buildlinkhub.example</div>
    <div class="rule"></div>
  </section>

  <section class="card card--back">
    <div class="back-brand">
      <p class="back-brand-name">BuildLinkHub.com</p>
      <p class="back-url">www.buildlinkhub.example</p>
    </div>
  </section>
</body>
</html>
```